Pellowar

We need logo and wesbsite for a software development company based out of Hyderabad, India focused on startups and mid sized companies focused on build a new software products in USA and Europe countires.

Target Market(s)

startup and midsized companies in teh USA and Europe for software product development.

Industry/Entity Type

software development

Coding

Coded - Design and coding required

Number of Pages Required

5+ page

Requirements
Must have
• latest design concepts and very elegant
Nice to have
• each page should have images that reflects the content
Should not have
• too many colors

```html
<!DOCTYPE html>
<html lang="en">
<head>
<meta charset="utf-8">
<title>Pellowar – Software Product Development</title>
<link href="https://fonts.googleapis.com/css2?family=Saira+Condensed:wght@400;600;700&family=Roboto:wght@400;500;700&display=swap" rel="stylesheet">
<style>
:root{
  --blue:#0a5db8;
  --blue-dark:#073a86;
  --blue-light:#1388cf;
  --ink:#1b1b1b;
  --text:#444;
  --black:#111;
  --grey-band:#eef0f3;
  --white:#fff;
}
*{box-sizing:border-box;margin:0;padding:0}
html,body{width:1200px;height:4858px;overflow:hidden}
body{position:relative;font-family:"Roboto",Arial,sans-serif;color:var(--text);background:var(--white);font-size:14px}
.abs{position:absolute}
.heading{font-family:"Saira Condensed","Arial Narrow",sans-serif}
.btn{position:absolute;display:flex;align-items:center;justify-content:center;background:linear-gradient(90deg,var(--blue-dark),var(--blue-light));color:#fff;font-family:"Saira Condensed",sans-serif;font-weight:700;font-size:13px;letter-spacing:.3px}
.btn-outline{background:transparent;border:2px solid #fff}
.topbar{left:0;top:0;width:1200px;height:57px;background:var(--black);color:#fff;font-size:13px}
.topbar .item{position:absolute;top:19px;display:flex;align-items:center;gap:12px}
.topbar .sep{position:absolute;top:8px;width:2px;height:41px;background:#fff}
.social{position:absolute;display:flex;gap:10px}
.social span{width:30px;height:30px;border:1.5px solid #fff;border-radius:50%;display:flex;align-items:center;justify-content:center}
.social span i{width:6px;height:6px;border-radius:50%;background:#fff}
.nav{left:0;top:57px;width:1200px;height:69px;background:#fff}
.logo{position:absolute;font-family:"Saira Condensed",sans-serif;font-weight:700;color:var(--blue);text-transform:uppercase}
.menu{position:absolute;left:336px;top:23px;display:flex;gap:30px;font-size:14px;color:var(--ink)}
.hero{left:0;top:126px;width:1200px;height:617px;background:linear-gradient(120deg,#e9ecee 0%,#f6f7f7 45%,#d9dde0 100%)}
.hero h1{position:absolute;left:0;width:1200px;top:220px;text-align:center;font-family:"Saira Condensed",sans-serif;font-weight:700;font-size:44px;color:var(--blue-dark)}
.hero p{position:absolute;left:0;width:1200px;top:276px;text-align:center;font-size:15px;line-height:29px;color:var(--ink)}
.arrow{position:absolute;width:38px;height:38px;border-radius:50%;background:var(--blue);display:flex;align-items:center;justify-content:center}
.label{position:absolute;padding-left:12px;border-left:3px solid var(--blue);font-family:"Saira Condensed",sans-serif;font-weight:600;font-size:17px;color:var(--ink);line-height:18px}
.big{position:absolute;font-family:"Saira Condensed",sans-serif;font-size:39px;line-height:51px;color:var(--ink)}
.big b{font-weight:700}
.para{position:absolute;font-size:14px;line-height:26px;color:var(--ink)}
.photo{position:absolute}
.product{left:0;top:1634px;width:1200px;height:840px;background:linear-gradient(100deg,#1184c9 0%,#0a5fb0 50%,#06378a 100%);color:#fff}
.sec-title{position:absolute;left:0;width:1200px;text-align:center;font-family:"Saira Condensed",sans-serif;font-weight:700;font-size:34px}
.sec-sub{position:absolute;left:0;width:1200px;text-align:center;font-size:14.5px;line-height:25px}
.hex{position:absolute;width:190px;height:210px}
.role{position:absolute;width:220px;text-align:center}
.role h3{font-family:"Saira Condensed",sans-serif;font-weight:600;font-size:25px;margin:4px 0}
.role p{font-size:13.5px;line-height:24px}
.vline{position:absolute;width:3px;background:#fff}
.team{left:0;top:3091px;width:1200px;height:706px;background:linear-gradient(100deg,#0a4c9e 0%,#0b62b4 55%,#138ad0 100%);color:#fff}
.card{position:absolute;top:240px;width:296px;height:368px;background:#fff;text-align:center}
.card .icon{position:absolute;left:99px;top:30px;width:98px;height:98px;border-radius:50%;background:linear-gradient(135deg,var(--blue-light),var(--blue-dark));display:flex;align-items:center;justify-content:center}
.card h4{position:absolute;top:143px;width:100%;font-family:"Saira Condensed",sans-serif;font-weight:600;font-size:20px;color:var(--blue)}
.card p{position:absolute;top:180px;left:22px;width:252px;font-size:13.5px;line-height:26px;color:#555}
.card .btn{top:298px;left:92px;width:112px;height:38px}
.form-card{left:477px;top:4019px;width:527px;height:355px;background:#fff;box-shadow:0 4px 24px rgba(0,0,0,.12)}
.field{position:absolute;width:186px}
.field label{display:block;font-family:"Saira Condensed",sans-serif;font-weight:700;font-size:11px;color:var(--ink)}
.field div{margin-top:10px;font-size:12.5px;color:var(--ink);padding-bottom:8px;border-bottom:1px solid #999}
.footer{left:0;top:4466px;width:1200px;height:392px;background:var(--black);color:#fff}
.footer h5{position:absolute;font-family:"Saira Condensed",sans-serif;font-weight:700;font-size:19px}
.footer .col{position:absolute;font-size:14px;line-height:30px}
.footer .info{position:absolute;display:flex;gap:16px;align-items:flex-start;font-size:14px;line-height:21px}
.pin{width:24px;height:24px;border-radius:50%;background:var(--blue);display:flex;align-items:center;justify-content:center;flex:none}
</style>
</head>
<body>

<div class="abs topbar">
  <div class="item" style="left:110px"><svg width="12" height="16" viewBox="0 0 12 16"><path d="M6 0a6 6 0 0 0-6 6c0 4.5 6 10 6 10s6-5.5 6-10a6 6 0 0 0-6-6zm0 8.5A2.5 2.5 0 1 1 6 3.5a2.5 2.5 0 0 1 0 5z" fill="#2a8be0"/></svg>0612 Lorem ipsum dolor sit amet</div>
  <div class="sep" style="left:402px"></div>
  <div class="item" style="left:453px"><svg width="18" height="13" viewBox="0 0 18 13"><rect width="18" height="13" rx="1.5" fill="#2a8be0"/><path d="M1 1l8 6 8-6" stroke="#111" stroke-width="1.5" fill="none"/></svg>info@pellowar.com</div>
  <div class="sep" style="left:668px"></div>
  <div class="item" style="left:717px"><svg width="16" height="16" viewBox="0 0 16 16"><path d="M3.5 0.5l3 3-1.8 2.2a10 10 0 0 0 5.6 5.6L12.5 9.5l3 3-2 2.5C6.5 15 1 9.5 1 2.5z" fill="#2a8be0"/></svg>+1 888 888 8888</div>
  <div class="social" style="left:930px;top:13px"><span><i></i></span><span><i></i></span><span><i></i></span><span><i></i></span></div>
</div>

<div class="abs nav">
  <div class="logo" style="left:111px;top:19px;font-size:24px">Pellowar</div>
  <nav class="menu"><span>Home</span><span>About</span><span>Build ur product</span><span>Build your team</span><span>Case study</span><span>Contact</span></nav>
  <div class="btn" style="left:966px;top:15px;width:106px;height:38px">LOG IN</div>
</div>

<section class="abs hero">
  <div class="photo" role="img" aria-label="Bright office desk with a monitor showing code, keyboard, phone and plant" style="left:0;top:0;width:1200px;height:617px;background:linear-gradient(120deg,#e6e9eb 0%,#f7f8f8 40%,#c9cfd4 75%,#e2e5e7 100%)"></div>
  <h1>WELCOME TO PELLOWAR</h1>
  <p>Teams are the essence of every business. They can create wonders if<br>built with perfection.</p>
  <div class="btn" style="left:545px;top:353px;width:111px;height:42px">GET STARTED</div>
  <div class="arrow" style="left:38px;top:291px"><svg width="12" height="14"><path d="M9 2L3 7l6 5" stroke="#fff" stroke-width="2.5" fill="none"/></svg></div>
  <div class="arrow" style="left:1128px;top:291px"><svg width="12" height="14"><path d="M3 2l6 5-6 5" stroke="#fff" stroke-width="2.5" fill="none"/></svg></div>
</section>

<div class="label" style="left:111px;top:834px">About Pellowar</div>
<div class="big" style="left:111px;top:868px">Teams are the <b>essence</b><br>of <b>every</b> business.</div>
<div class="para" style="left:551px;top:830px;width:545px">We are a group of entrepreneurs, technocrats, software architects, and delivery<br>heads who have come together to serve startups,</div>
<div class="para" style="left:551px;top:889px;width:545px">product companies, and enterprises with their product development.<br>We are prompt in understanding your product and help design, build, maintain<br>and operate your product.</div>
<div class="btn" style="left:551px;top:981px;width:111px;height:40px">READ MORE</div>

<div class="abs" style="left:111px;top:1057px;width:619px;height:492px;border:3px solid var(--blue-dark);border-bottom:none;border-right:none"></div>
<div class="abs" style="left:727px;top:1057px;width:3px;height:22px;background:var(--blue-dark)"></div>
<div class="photo" role="img" aria-label="Smiling team of colleagues standing together in an office" style="left:134px;top:1079px;width:660px;height:319px;background:linear-gradient(135deg,#8a7a6e,#c7b9a8 45%,#4e6c78 100%)"></div>
<div class="photo" role="img" aria-label="Developers working at computers in an open office" style="left:676px;top:1247px;width:369px;height:302px;background:linear-gradient(135deg,#d9dde0,#8e979e 55%,#3f474d 100%)"></div>
<div class="abs" style="left:134px;top:1424px;width:3px;height:123px;background:var(--blue)"></div>
<div class="abs heading" style="left:151px;top:1420px;font-weight:600;font-size:18px;color:var(--ink)">How can you build software with us</div>
<div class="para" style="left:154px;top:1450px;width:450px;font-size:13.5px">Brainstorm for a product that will solve a problem.Plan the entire<br>process.Incorporate ideas from business partners or stake holders.<br>Design the product.Outsource the development team.Develop the<br>product.</div>

<section class="abs product">
  <div class="sec-title" style="top:76px">BUILD YOUR PRODUCT</div>
  <div class="sec-sub" style="top:134px">As startups are racing to build software as a product, they have stumbling blocks on building software from scratch.<br>One of the reasons is stiff competition.</div>

  <svg class="hex" style="left:113px;top:242px" viewBox="0 0 190 210"><polygon points="95,3 187,55 187,155 95,207 3,155 3,55" fill="none" stroke="#fff" stroke-width="4"/><polygon points="95,16 175,62 175,148 95,194 15,148 15,62" fill="#fff"/><polygon points="95,24 168,66 168,144 95,186 22,144 22,66" fill="var(--blue-dark)"/><circle cx="82" cy="92" r="14" fill="#fff"/><path d="M58 140c0-20 10-30 24-30s24 10 24 30z" fill="#fff"/><circle cx="120" cy="118" r="13" fill="none" stroke="#fff" stroke-width="5" stroke-dasharray="5 3"/><rect x="112" y="78" width="4" height="18" fill="#fff"/><rect x="120" y="84" width="4" height="12" fill="#fff"/></svg>
  <svg class="hex" style="left:631px;top:242px" viewBox="0 0 190 210"><polygon points="95,3 187,55 187,155 95,207 3,155 3,55" fill="none" stroke="#fff" stroke-width="4"/><polygon points="95,16 175,62 175,148 95,194 15,148 15,62" fill="#fff"/><polygon points="95,24 168,66 168,144 95,186 22,144 22,66" fill="var(--blue-dark)"/><rect x="62" y="70" width="52" height="68" fill="none" stroke="#fff" stroke-width="4"/><rect x="70" y="116" width="6" height="16" fill="#fff"/><rect x="80" y="108" width="6" height="24" fill="#fff"/><rect x="90" y="112" width="6" height="20" fill="#fff"/><path d="M70 82h34M70 92h34" stroke="#fff" stroke-width="3"/><circle cx="118" cy="110" r="11" fill="#fff"/><path d="M98 145c0-15 8-23 20-23s20 8 20 23z" fill="#fff"/></svg>
  <svg class="hex" style="left:371px;top:444px" viewBox="0 0 190 210"><polygon points="95,3 187,55 187,155 95,207 3,155 3,55" fill="none" stroke="#fff" stroke-width="4"/><polygon points="95,16 175,62 175,148 95,194 15,148 15,62" fill="#fff"/><polygon points="95,24 168,66 168,144 95,186 22,144 22,66" fill="var(--blue-dark)"/><circle cx="95" cy="76" r="11" fill="#fff"/><path d="M80 92h30v34h-8v22h-14v-22h-8z" fill="#fff"/><circle cx="62" cy="96" r="9" fill="#fff"/><rect x="52" y="108" width="20" height="38" fill="#fff"/><circle cx="128" cy="96" r="9" fill="#fff"/><rect x="118" y="108" width="20" height="38" fill="#fff"/></svg>
  <svg class="hex" style="left:890px;top:444px" viewBox="0 0 190 210"><polygon points="95,3 187,55 187,155 95,207 3,155 3,55" fill="none" stroke="#fff" stroke-width="4"/><polygon points="95,16 175,62 175,148 95,194 15,148 15,62" fill="#fff"/><polygon points="95,24 168,66 168,144 95,186 22,144 22,66" fill="var(--blue-dark)"/><rect x="72" y="66" width="46" height="44" rx="20" fill="#fff"/><rect x="70" y="84" width="50" height="10" rx="4" fill="none" stroke="var(--blue-dark)" stroke-width="3"/><path d="M58 150c0-22 14-32 37-32s37 10 37 32z" fill="#fff"/><path d="M85 128l-6 6 6 6M105 128l6 6-6 6M98 126l-6 16" stroke="var(--blue-dark)" stroke-width="3" fill="none"/></svg>

  <div class="role" style="left:98px;top:527px"><h3>Project Manage</h3><p>Lorem ipsum dolor sit amet,<br>consectetur adipiscing elit, sed<br>do eiusmod tempor incididunt</p></div>
  <div class="role" style="left:356px;top:246px"><p>Lorem ipsum dolor sit amet,<br>consectetur adipiscing elit, sed<br>do eiusmod tempor incididunt</p><h3>Team Lead</h3></div>
  <div class="vline" style="left:465px;top:382px;height:62px"></div>
  <div class="vline" style="left:724px;top:452px;height:62px"></div>
  <div class="role" style="left:616px;top:527px"><h3>Business analyst</h3><p>Lorem ipsum dolor sit amet,<br>consectetur adipiscing elit, sed<br>do eiusmod tempor incididunt</p></div>
  <div class="role" style="left:875px;top:246px"><p>Lorem ipsum dolor sit amet,<br>consectetur adipiscing elit, sed<br>do eiusmod tempor incididunt</p><h3>Developers</h3></div>
  <div class="vline" style="left:984px;top:382px;height:62px"></div>

  <div class="btn btn-outline" style="left:568px;top:706px;width:113px;height:45px">SEE MORE</div>
</section>

<div class="label" style="left:111px;top:2559px">Case study</div>
<div class="big" style="left:111px;top:2592px;line-height:51px"><b>Many business</b> owners<br>have great ideas <b>but no</b><br><b>experience</b></div>
<div class="para" style="left:111px;top:2757px;width:464px;text-align:justify">Once you have an idea in mind, you will require software development aid at some point – whether your concept is for next-generation software or an inventive approach to offering an existing service.</div>
<div class="para" style="left:111px;top:2864px;width:464px;text-align:justify">It might also be the development of a mobile app or web-based software. Whatever product you're working on, you'll need a technical co-founder to help you get it off the ground. An MVP can help you</div>
<div class="btn" style="left:111px;top:2964px;width:110px;height:42px">READ MORE</div>
<div class="abs" style="left:617px;top:2559px;width:430px;height:422px;border:3px solid var(--blue-dark);border-bottom:none;border-right:none"></div>
<div class="abs" style="left:1044px;top:2559px;width:3px;height:19px;background:var(--blue-dark)"></div>
<div class="photo" role="img" aria-label="Two colleagues reviewing work together at a computer desk" style="left:638px;top:2578px;width:449px;height:403px;background:linear-gradient(135deg,#c9c3bc,#8c8a88 50%,#3b4a5c 100%)"></div>

<section class="abs team">
  <div class="sec-title" style="top:94px">BUILD YOUR TEAM</div>
  <div class="sec-sub" style="top:148px">Break free from traditional recruiting with us. At Pellowar, we help you achieve the right organizational matrix<br>with rockstars who can take your business to the next level.</div>
  <div class="card" style="left:113px">
    <div class="icon"><svg width="52" height="52" viewBox="0 0 52 52"><path d="M26 6c-11 0-18 8-18 17 0 6 3 9 5 12v11h17v-5h7c2 0 3-1 3-3v-6h4l-4-8C40 13 34 6 26 6z" fill="none" stroke="#fff" stroke-width="3"/><circle cx="25" cy="22" r="7" fill="none" stroke="#fff" stroke-width="3"/></svg></div>
    <h4>Pass Cognitive Aptitude Test.</h4>
    <p>Accepting job applications from the entire world means every role on Stackvale receives thousands of applications. We find that the most</p>
    <div class="btn">READ MORE</div>
  </div>
  <div class="card" style="left:455px">
    <div class="icon"><svg width="52" height="52" viewBox="0 0 52 52"><path d="M8 44l14-4-10-10z" fill="#fff"/><path d="M12 30l24-22 8 8-22 24z" fill="none" stroke="#fff" stroke-width="3"/><path d="M40 32l2 4 4 1-3 3 1 4-4-2-4 2 1-4-3-3 4-1z" fill="#fff"/></svg></div>
    <h4>Pass English Proficiency Test.</h4>
    <p>Someday, technological advancements will make it possible for teams to collaborate without sharing a common language. Until</p>
    <div class="btn">READ MORE</div>
  </div>
  <div class="card" style="left:796px">
    <div class="icon"><svg width="52" height="52" viewBox="0 0 52 52"><rect x="6" y="15" width="40" height="28" rx="3" fill="none" stroke="#fff" stroke-width="3"/><path d="M19 15v-5h14v5M6 26h40" stroke="#fff" stroke-width="3" fill="none"/><rect x="22" y="23" width="8" height="6" fill="#fff"/></svg></div>
    <h4>Prove Real-World Job Skills</h4>
    <p>Of course, there's much more to being a great worker than intelligence and language skills. The next step is to complete a real-world</p>
    <div class="btn">READ MORE</div>
  </div>
</section>

<div class="abs" style="left:0;top:4259px;width:1200px;height:207px;background:var(--grey-band)"></div>
<div class="sec-title abs heading" style="top:3876px;color:var(--blue-dark)">CONTACT US</div>
<div class="abs" style="left:174px;top:4042px;width:379px;height:260px;background:linear-gradient(135deg,var(--blue-dark),var(--blue-light))"></div>
<div class="abs" style="left:268px;top:4048px;font-size:21px;font-weight:500;color:#fff">Contact us</div>
<div class="abs heading" style="left:268px;top:4092px;font-size:42px;line-height:46px;color:#fff;text-align:right;width:154px">Let's Do<br>Good<br>Together!</div>
<div class="abs" style="left:711px;top:4042px;width:317px;height:40px;border:3px solid var(--blue-dark);border-bottom:none;border-left:none"></div>
<div class="abs" style="left:711px;top:4042px;width:3px;height:14px;background:var(--blue-dark)"></div>
<div class="abs form-card">
  <div class="abs heading" style="left:50px;top:36px;font-weight:600;font-size:32px;color:var(--ink)">Send Us A Message</div>
  <div class="field" style="left:50px;top:110px"><label>YOUR NAME</label><div>ARLO</div></div>
  <div class="field" style="left:283px;top:110px"><label>LAST NAME</label><div>VENN</div></div>
  <div class="field" style="left:50px;top:190px"><label>EMAIL ADDRESS</label><div>arlo.venn@example.com</div></div>
  <div class="field" style="left:283px;top:190px"><label>PHONE</label><div>123 456 7890</div></div>
  <div class="field" style="left:50px;top:270px;width:338px"><label>MESSAGE</label><div>Hi, do you have a moment to talk abo....|</div></div>
  <div class="abs" style="left:412px;top:267px;width:48px;height:48px;border-radius:50%;background:linear-gradient(135deg,var(--blue-light),var(--blue-dark));display:flex;align-items:center;justify-content:center"><svg width="20" height="20" viewBox="0 0 20 20"><path d="M2 9l16-7-6 16-3-6z" fill="#fff"/></svg></div>
</div>
<div class="abs" style="left:1098px;top:4475px;width:58px;height:58px;border-radius:50%;background:var(--blue);border:3px solid #fff;display:flex;align-items:center;justify-content:center;z-index:2"><svg width="28" height="24" viewBox="0 0 28 24"><path d="M3 2h22v15H11l-6 5v-5H3z" fill="#fff"/><circle cx="9" cy="10" r="1.8" fill="#0a5db8"/><circle cx="14" cy="10" r="1.8" fill="#0a5db8"/><circle cx="19" cy="10" r="1.8" fill="#0a5db8"/></svg></div>

<footer class="abs footer">
  <div class="logo" style="left:85px;top:72px;font-size:27px;color:#1e7ad6">Pellowar</div>
  <div class="col" style="left:85px;top:112px;width:230px;font-size:13.5px;line-height:29px">All top-notch companies employ a Minimum Viable Product (MVP) methodology to not only assess the</div>
  <h5 style="left:359px;top:70px">QUICK LINK</h5>
  <div class="col" style="left:364px;top:112px">Home<br>About<br>Build ur product<br>Build your team<br>Case study<br>Contact</div>
  <div class="col" style="left:518px;top:112px">Terms<br>condtions<br>Privacy Policy<br>Support<br>Blog<br>Meet Our Team</div>
  <h5 style="left:677px;top:70px">CONTACT US</h5>
  <div class="info" style="left:675px;top:112px"><span class="pin"><svg width="10" height="13" viewBox="0 0 12 16"><path d="M6 0a6 6 0 0 0-6 6c0 4.5 6 10 6 10s6-5.5 6-10a6 6 0 0 0-6-6z" fill="#fff"/></svg></span><span>123, Lorem ipsum<br>dolor, IL 200306</span></div>
  <div class="info" style="left:675px;top:175px"><span class="pin"><svg width="12" height="9" viewBox="0 0 18 13"><rect width="18" height="13" fill="#fff"/><path d="M1 1l8 6 8-6" stroke="#0a5db8" stroke-width="1.5" fill="none"/></svg></span><span>info@pellowar.in</span></div>
  <div class="info" style="left:675px;top:222px"><span class="pin"><svg width="11" height="11" viewBox="0 0 16 16"><path d="M3.5 0.5l3 3-1.8 2.2a10 10 0 0 0 5.6 5.6L12.5 9.5l3 3-2 2.5C6.5 15 1 9.5 1 2.5z" fill="#fff"/></svg></span><span>+1 888 888 8888</span></div>
  <h5 style="left:919px;top:70px">NEWSLETTER</h5>
  <div class="col" style="left:921px;top:108px;width:200px;font-size:13.5px;line-height:22px">Sign up for our latest news &amp; articles.</div>
  <div class="abs" style="left:921px;top:170px;width:191px;height:40px;border:1.5px solid #fff;display:flex;align-items:center;justify-content:space-between;padding:0 14px"><span class="heading" style="font-weight:700;font-size:10px">YOUR EMAIL</span><svg width="14" height="10" viewBox="0 0 18 13"><rect width="18" height="13" fill="#fff"/><path d="M1 1l8 6 8-6" stroke="#111" stroke-width="1.5" fill="none"/></svg></div>
  <div class="abs" style="left:0;top:323px;width:1200px;height:1px;background:#555"></div>
  <div class="abs" style="left:0;top:347px;width:1200px;text-align:center;font-size:13.5px">©Copyrights 2022 pellowar LLC | &nbsp; All Rights Reserved</div>
  <div class="social" style="left:924px;top:340px"><span><i></i></span><span><i></i></span><span><i></i></span><span><i></i></span></div>
</footer>

</body>
</html>
```